Travel Agency Website - Simple General

Need a 7 page simple design that is pretty repetitive. Need to be able to load quickly that is SEO optimized. Trying to give ideas on what they can do, be personal as we are local, but at the same time come across as professional and get information easily with little burden.

- Landing Page
- Brimwell Vacations Page
- Family Trips
- Road Trips from Texas
- Other Destinations
- About Us Page
- Contact Us Page

Target Market(s)

Families

Coding

Coded - Design and coding required

Number of Pages Required

5+ page

Colors

Designer to choose colors to be used in the design.

Requirements
Must have
• Like it to flow easily with our logo. Use that for colors, etc.

```html
<!DOCTYPE html>
<html lang="en">
<head>
<meta charset="utf-8">
<title>Wayfare Lane Travel – Family Vacations, Road Trips &amp; More</title>
<meta name="description" content="Custom Brimwell vacations, family trips, and road trips from Texas designed with care by Wayfare Lane Travel.">
<link rel="stylesheet" href="https://fonts.googleapis.com/css2?family=Playfair+Display:wght@500;600;700&family=Lato:wght@400;700&display=swap">
<style>
:root{
  --teal:#2a7a82;
  --teal-deep:#1e5a63;
  --gold:#c4994f;
  --gold-light:#d9b577;
  --mist:#e3eff0;
  --ink:#2b2b2b;
  --night:#060e10;
  --white:#ffffff;
}
*{box-sizing:border-box;margin:0;padding:0}
html,body{width:1200px;height:4075px;overflow:hidden}
body{position:relative;font-family:"Lato",sans-serif;color:var(--ink);background:var(--white)}
a{color:inherit;text-decoration:none}
.abs{position:absolute}

/* hero */
.hero-photo{position:absolute;left:0;top:0;width:1200px;height:760px;
  background:linear-gradient(180deg,#dfe3e4 0%,#e9e4dc 30%,#cdb393 50%,#c2a37d 75%,#b79a76 100%)}
.hero-vehicle{position:absolute;left:585px;top:110px;width:615px;height:470px;border-radius:40px 40px 20px 20px;
  background:linear-gradient(160deg,#d8d8d6,#8e8b86 60%,#4b4744)}
.waves{position:absolute;left:0;top:0}
.logo{position:absolute;left:114px;top:70px;display:flex;align-items:center;gap:10px}
.logo-dot{width:18px;height:18px;border-radius:50%;background:var(--teal)}
.logo-name{font-family:"Playfair Display",serif;font-weight:600;font-size:28px;color:var(--teal-deep);line-height:1.1}
.nav{position:absolute;top:42px;left:373px;display:flex;gap:33px;font-size:14px;color:#3d4a4c}
.nav .active{color:var(--teal);font-weight:700}
.hero-title{position:absolute;left:113px;top:238px;font-family:"Playfair Display",serif;font-weight:600;font-size:46px;line-height:48px}
.hero-title .lead{color:var(--gold)}
.hero-title .main{color:var(--teal-deep)}
.hero-copy{position:absolute;left:114px;top:363px;width:456px;font-size:19px;line-height:27px;color:#333;text-align:justify}
.btn{position:absolute;display:flex;align-items:center;justify-content:center;height:42px;border-radius:21px;
  color:var(--white);font-size:15px;background:var(--gold)}
.btn.teal{background:var(--teal)}

/* section headings */
.section-title{position:absolute;left:0;width:1200px;text-align:center;font-family:"Playfair Display",serif;
  font-weight:600;font-size:42px;color:var(--teal-deep)}
.section-title::after{content:"";display:block;width:52px;height:3px;background:var(--gold);margin:4px auto 0}
.center-copy{position:absolute;left:190px;width:820px;text-align:center;font-size:16px;line-height:26px;color:#333}

/* feature rows */
.feature-photo{position:absolute;width:406px;height:406px}
.feature-photo::before{content:"";position:absolute;left:8px;top:8px;width:100%;height:100%;border-radius:50%;background:var(--teal)}
.feature-photo.gold::before{left:-8px;background:var(--gold)}
.feature-photo .fill{position:absolute;inset:0;border-radius:50%;border:4px solid var(--white)}
.feature-title{position:absolute;font-family:"Playfair Display",serif;font-weight:600;font-size:33px;color:var(--teal)}
.feature-copy{position:absolute;width:488px;font-size:16px;line-height:25.6px;color:#333;text-align:justify}
.feature-copy p+p{margin-top:26px}

/* footer */
.footer{position:absolute;left:0;top:3560px;width:1200px;height:515px;background:var(--night);color:var(--white)}
.footer-col{position:absolute;top:150px}
.footer-col h3{font-weight:700;font-size:21px;margin-bottom:28px}
.footer-col li{list-style:none;font-size:15px;line-height:38.5px}
.footer-note{font-size:14px;line-height:23px;width:290px}
.subscribe-field{width:274px;height:41px;border-radius:21px;background:var(--white);color:#333;font-size:15px;
  padding-left:28px;display:flex;align-items:center;margin-top:26px}
.contact-row{display:flex;gap:18px;font-size:15px;line-height:25px;margin-bottom:36px}
.contact-row svg{flex:none;margin-top:4px}
.footer-rule{position:absolute;left:111px;top:463px;width:978px;height:1px;background:#2a3335}
.copyright{position:absolute;left:0;top:480px;width:1200px;text-align:center;font-size:13px}
</style>
</head>
<body>

<header>
  <div class="hero-photo" role="img" aria-label="Family of three sitting in the open back of a white SUV on a sandy beach"></div>
  <div class="hero-vehicle" role="img" aria-label="White SUV with open tailgate and family seated inside"></div>

  <svg class="waves" width="1200" height="1320" viewBox="0 0 1200 1320" aria-hidden="true">
    <path d="M0 690 C120 740 260 750 420 720 C620 680 820 630 980 640 C1080 646 1150 665 1200 690 L1200 1205 C1000 1190 800 1220 600 1250 C400 1280 180 1290 0 1250 Z" fill="#e3eff0"/>
    <path d="M60 720 C200 760 330 750 480 720 C680 680 860 635 1010 645" fill="none" stroke="#2a7a82" stroke-width="7"/>
    <path d="M1000 643 C1100 650 1160 672 1200 695" fill="none" stroke="#2a7a82" stroke-width="2"/>
    <path d="M0 1252 C180 1292 400 1282 600 1252 C800 1222 1000 1192 1200 1206 L1200 1320 L0 1320 Z" fill="#ffffff"/>
    <path d="M200 1292 C420 1290 620 1250 820 1220 C960 1200 1080 1196 1200 1206" fill="none" stroke="#cfe0e2" stroke-width="2"/>
  </svg>

  <a class="logo" href="#"><span class="logo-dot"></span><span class="logo-name">Wayfare Lane<br>Travel</span></a>

  <nav class="nav">
    <a class="active" href="#">Home</a>
    <a href="#">Brimwell Vacations</a>
    <a href="#">Family Trips</a>
    <a href="#">Road Trips from Texas</a>
    <a href="#">Other Destinations</a>
    <a href="#">About Us</a>
  </nav>

  <h1 class="hero-title"><span class="lead">Adventure Starts</span><br><span class="main">the Moment You Wander</span></h1>
  <p class="hero-copy">Custom Brimwell vacations, unforgettable family trips, and road trip adventures designed with care, excitement, and zero stress.</p>
  <a class="btn teal" href="#" style="left:114px;top:470px;width:136px">Contact Us</a>
  <a class="btn" href="#" style="left:259px;top:469px;width:162px">Start Planning</a>
</header>

<main>
  <section>
    <h2 class="section-title" style="top:805px">About Us</h2>
    <div class="center-copy" style="top:890px">
      <p>At Wayfare Lane Travel, we specialize in planning magical Brimwell vacations, family-friendly getaways, scenic road trips from Texas, and unforgettable destination experiences tailored to every traveler’s style. Our goal is to make travel planning simple, exciting, and stress-free.</p>
      <p style="margin-top:26px">Whether you're planning your child’s first Brimwell adventure, a relaxing beach escape, or a memorable road trip packed with hidden gems, we create personalized experiences designed around your family’s needs, budget, and travel dreams.</p>
    </div>
    <a class="btn" href="#" style="left:530px;top:1101px;width:137px">Read More</a>
  </section>

  <section>
    <h2 class="section-title" style="top:1356px">Explore Your Next Adventure</h2>
    <p class="center-copy" style="top:1434px;left:210px;width:780px">Discover personalized travel experiences designed for magical memories, family fun, scenic road trips, and unforgettable destinations around the world.</p>

    <div class="feature-photo" style="left:114px;top:1576px">
      <div class="fill" role="img" aria-label="Costumed performer in a white dress at a theme park parade" style="background:linear-gradient(160deg,#6e9bd4,#f2f2f0 55%,#5b6a8a)"></div>
    </div>
    <h3 class="feature-title" style="left:601px;top:1586px">Brimwell Vacations</h3>
    <div class="feature-copy" style="left:601px;top:1648px">
      <p>Lorem ipsum dolor sit amet, consectetur adipiscing elit, sed do eiusmod tempor incididunt ut labore et dolore magna aliqua. Ut enim ad minim veniam, quis nostrud exercitation ullamco laboris nisi ut aliquip ex ea commodo consequat.</p>
      <p>Duis aute irure dolor in reprehenderit in voluptate velit esse cillum dolore eu fugiat nulla pariatur. Excepteur sint occaecat cupidatat non proident, sunt in culpa qui officia deserunt mollit anim id est laborum.</p>
    </div>
    <a class="btn" href="#" style="left:602px;top:1911px;width:206px">Explore Brimwell Magic</a>

    <h3 class="feature-title" style="left:112px;top:2063px">Family Trips</h3>
    <div class="feature-copy" style="left:112px;top:2125px">
      <p>Lorem ipsum dolor sit amet, consectetur adipiscing elit, sed do eiusmod tempor incididunt ut labore et dolore magna aliqua. Ut enim ad minim veniam, quis nostrud exercitation ullamco laboris nisi ut aliquip ex ea commodo consequat.</p>
      <p>Duis aute irure dolor in reprehenderit in voluptate velit esse cillum dolore eu fugiat nulla pariatur. Excepteur sint occaecat cupidatat non proident, sunt in culpa qui officia deserunt mollit anim id est laborum.</p>
    </div>
    <a class="btn" href="#" style="left:114px;top:2389px;width:163px">Plan Family Fun</a>
    <div class="feature-photo gold" style="left:690px;top:2052px">
      <div class="fill" role="img" aria-label="Family playing together on the beach at sunset" style="background:linear-gradient(180deg,#c9d6e0 0%,#9fb4c4 45%,#4b6f86 55%,#c8ab86 75%,#9d7f60)"></div>
    </div>

    <div class="feature-photo" style="left:114px;top:2530px">
      <div class="fill" role="img" aria-label="Red canyon landscape under a blue sky in Texas" style="background:linear-gradient(180deg,#3d6fb8 0%,#9dbbe0 35%,#c0653a 50%,#5c7a3d 68%,#c7824a 100%)"></div>
    </div>
    <h3 class="feature-title" style="left:601px;top:2539px">Texas Road Trips</h3>
    <div class="feature-copy" style="left:601px;top:2601px">
      <p>Lorem ipsum dolor sit amet, consectetur adipiscing elit, sed do eiusmod tempor incididunt ut labore et dolore magna aliqua. Ut enim ad minim veniam, quis nostrud exercitation ullamco laboris nisi ut aliquip ex ea commodo consequat.</p>
      <p>Duis aute irure dolor in reprehenderit in voluptate velit esse cillum dolore eu fugiat nulla pariatur. Excepteur sint occaecat cupidatat non proident, sunt in culpa qui officia deserunt mollit anim id est laborum.</p>
    </div>
    <a class="btn" href="#" style="left:602px;top:2865px;width:198px">Start Your Road Trip</a>

    <h3 class="feature-title" style="left:112px;top:3016px">Other Destinations</h3>
    <div class="feature-copy" style="left:112px;top:3078px">
      <p>Lorem ipsum dolor sit amet, consectetur adipiscing elit, sed do eiusmod tempor incididunt ut labore et dolore magna aliqua. Ut enim ad minim veniam, quis nostrud exercitation ullamco laboris nisi ut aliquip ex ea commodo consequat.</p>
      <p>Duis aute irure dolor in reprehenderit in voluptate velit esse cillum dolore eu fugiat nulla pariatur. Excepteur sint occaecat cupidatat non proident, sunt in culpa qui officia deserunt mollit anim id est laborum.</p>
    </div>
    <a class="btn" href="#" style="left:114px;top:3342px;width:206px">Explore Destinations</a>
    <div class="feature-photo gold" style="left:690px;top:3006px">
      <div class="fill" role="img" aria-label="Couple walking with luggage through a sunny old-town street" style="background:linear-gradient(160deg,#e6d2bf,#b89a7d 45%,#7a6a5e 80%,#5a4d45)"></div>
    </div>
  </section>
</main>

<svg class="abs" style="left:0;top:3480px" width="1200" height="90" viewBox="0 0 1200 90" aria-hidden="true">
  <path d="M0 70 C150 40 300 30 520 50 C760 72 980 88 1200 30 L1200 90 L0 90 Z" fill="#060e10"/>
  <path d="M70 40 C250 20 420 25 600 45 C780 65 960 85 1200 28" fill="none" stroke="#2a7a82" stroke-width="7"/>
</svg>

<footer class="footer">
  <div class="footer-col" style="left:111px">
    <h3>Stay Inspired</h3>
    <p class="footer-note">Get travel tips, destination ideas, Brimwell updates, and family vacation inspiration delivered to your inbox.</p>
    <div class="subscribe-field">Enter Your Email</div>
    <a class="btn" href="#" style="position:relative;width:146px;margin-top:14px">Subscribe</a>
  </div>
  <div class="footer-col" style="left:465px">
    <h3>Main Links</h3>
    <ul><li>Home</li><li>Brimwell Vacations</li><li>Family Trips</li><li>Road Trips from Texas</li><li>Other Destinations</li></ul>
  </div>
  <div class="footer-col" style="left:702px">
    <h3>Contact Us</h3>
    <div class="contact-row">
      <svg width="20" height="22" viewBox="0 0 20 22" fill="none" stroke="#fff" stroke-width="1.6"><path d="M10 21s7-7 7-12a7 7 0 0 0-14 0c0 5 7 12 7 12z"/><circle cx="10" cy="9" r="2.5"/></svg>
      <span>48 Harbor Row, Suite 3,<br>Austin, TX 78701</span>
    </div>
    <div class="contact-row">
      <svg width="20" height="20" viewBox="0 0 20 20" fill="none" stroke="#fff" stroke-width="1.6"><path d="M4 2l3 0 1.5 4-2 1.5a11 11 0 0 0 6 6l1.5-2 4 1.5v3a2 2 0 0 1-2 2A16 16 0 0 1 2 4a2 2 0 0 1 2-2z"/></svg>
      <span>555-014-2288</span>
    </div>
    <div class="contact-row">
      <svg width="20" height="16" viewBox="0 0 20 16" fill="none" stroke="#fff" stroke-width="1.6"><rect x="1" y="1" width="18" height="14" rx="2"/><path d="M1 3l9 6 9-6"/></svg>
      <span>hello@wayfarelane.example</span>
    </div>
  </div>
  <div class="footer-col" style="left:969px">
    <h3>Other Links</h3>
    <ul><li>About Us</li><li>Contact Us</li><li>Privacy Policy</li><li>Terms &amp; Services</li><li>Cookie Policy</li></ul>
  </div>
  <div class="footer-rule"></div>
  <p class="copyright">Copyright © 2026 Wayfare Lane Travel. All rights reserved.</p>
</footer>

</body>
</html>
```